Business Card Design

We are a commercial real estate brokerage in San Francisco, leasing office buildings downtown.
I would like a clean, elegant look. Simple but powerful .

Industry/Entity Type

Business

Contact Information for Business Card

Derek Holloway
lic# 07258143
415.555.0172
derek@velt-commercial.example
velt-commercial.example

```html
<!DOCTYPE html>
<html lang="en">
<head>
<meta charset="utf-8">
<title>Velt Commercial – Business Card</title>
<link rel="stylesheet" href="https://fonts.googleapis.com/css2?family=Oswald:wght@300;400&display=swap">
<style>
  :root {
    --backdrop: #e6e2da;
    --card-edge: #ffffff;
    --card-face: #ebebeb;
    --tile: #8a8a8a;
    --tile-text: #ffffff;
    --brand: #6f7f99;
    --font: "Oswald", sans-serif;
  }
  * { box-sizing: border-box; margin: 0; padding: 0; }
  html, body {
    width: 1200px; height: 510px; overflow: hidden;
    background: var(--backdrop);
    font-family: var(--font);
  }
  .canvas { position: relative; width: 1200px; height: 510px; }

  .card {
    position: absolute; top: 133px;
    width: 417px; height: 245px;
    background: var(--card-edge);
    padding: 11px;
  }
  .card--front { left: 158px; }
  .card--back { left: 625px; }

  .front-face {
    width: 100%; height: 100%;
    background: var(--card-face);
    display: flex; align-items: center; justify-content: center;
  }
  .brand { display: flex; align-items: center; gap: 10px; }
  .brand__square { width: 16px; height: 16px; background: var(--brand); }
  .brand__name {
    font-weight: 400; font-size: 24px; letter-spacing: 1px;
    color: var(--brand); text-transform: uppercase;
  }

  .back-face {
    width: 100%; height: 100%;
    display: grid;
    grid-template-columns: repeat(4, 1fr);
    grid-template-rows: 114px 1fr;
    gap: 4px;
  }
  .back-face > div { background: var(--tile); color: var(--tile-text); }
  .holder-name {
    grid-column: 1 / 5;
    display: flex; align-items: center; justify-content: center;
    font-weight: 300; font-size: 17px; letter-spacing: 0.5px;
    text-transform: uppercase;
  }
  .contact {
    display: flex; flex-direction: column; align-items: center; justify-content: center;
    gap: 6px; font-weight: 300; font-size: 7.5px; white-space: nowrap;
  }
  .contact svg { width: 11px; height: 11px; fill: none; stroke: var(--tile-text); stroke-width: 1.2; }
  .contact--licence { padding-top: 0; }
</style>
</head>
<body>
<main class="canvas">
  <section class="card card--front" aria-label="Card front">
    <div class="front-face">
      <div class="brand">
        <span class="brand__square"></span>
        <span class="brand__name">Velt Commercial</span>
      </div>
    </div>
  </section>

  <section class="card card--back" aria-label="Card back">
    <div class="back-face">
      <div class="holder-name">Derek Holloway</div>
      <div class="contact contact--licence"><span>lic# 07258143</span></div>
      <div class="contact">
        <svg viewBox="0 0 12 12" aria-hidden="true"><rect x="3.5" y="0.8" width="5" height="10.4" rx="0.8"/><line x1="5.4" y1="9.6" x2="6.6" y2="9.6"/></svg>
        <span>415.555.0172</span>
      </div>
      <div class="contact">
        <svg viewBox="0 0 12 12" aria-hidden="true"><rect x="0.8" y="2.5" width="10.4" height="7" /><polyline points="0.8,2.5 6,6.6 11.2,2.5"/></svg>
        <span>derek@velt-commercial.example</span>
      </div>
      <div class="contact">
        <svg viewBox="0 0 12 12" aria-hidden="true"><circle cx="6" cy="6" r="5.2"/><ellipse cx="6" cy="6" rx="2.2" ry="5.2"/><line x1="0.8" y1="6" x2="11.2" y2="6"/></svg>
        <span>velt-commercial.example</span>
      </div>
    </div>
  </section>
</main>
</body>
</html>
```